Stationery Design Project for Nimbora, Chicago

Nimbora, a street parking application which helps car drivers find a street parking spot by offering an ideal path along which to look for parking. This path is calculated by our algorithm based on data (e.g. historical data, baseball games schedule, etc.). Along this path the driver will find a spot and will also save 70% of the search time. Customer we target is reg. between 21 and 45 yo.

We envision something young, fresh, bright and original. Slightly abstract maybe. It should represent the idea and elements of finding street parking in the city, e.g. car(s), parking spot, people, city, etc. (just ideas!).

Logo is attached.

Requirement:
- Business Cards (2 Sided Full Color CMYK)
- Letterhead (1 Sided Full Color CMYK)
- Envelope (1 Sided Full Color CMYK)
- Sticker (1 Sided Full Color CMYK), round with a 2inch diameter.

Reason: We're starting to get more and more designs and need more time to look into all of them. Very exciting!! Thanks to everybody!

Hi all, we're in the process of selecting our favs. Though choices!!! Really good submissions. Will keep you posted and sorry for the delay.

Target Market(s)

Car drivers and owners between 21 and 45

Industry/Entity Type

Parking

Requirements
Must have
• Sticker should be round and include company URL nimbora.com and the new logo which we will attach soon.
Should not have
• Should not be too serious or boring.

```html
<!DOCTYPE html>
<html lang="en">
<head>
<meta charset="utf-8">
<title>Nimbora Business Card</title>
<link rel="stylesheet" href="https://fonts.googleapis.com/css2?family=Open+Sans:wght@400;600;700&display=swap">
<style>
  :root {
    --page-bg: #e9ebee;
    --card-white: #ffffff;
    --ink-dark: #1f1f22;
    --blue-deep: #2b47a3;
    --blue-mid: #2f6fc4;
    --blue-light: #35a6e2;
    --divider: #2a2a30;
    --text-on-blue: #ffffff;
    --photo-grey: #9aa3aa;
    --photo-dark: #5d6770;
    --photo-light: #c9cfd4;
  }
  * { box-sizing: border-box; margin: 0; padding: 0; }
  html, body {
    width: 1200px; height: 758px; overflow: hidden;
    background: var(--page-bg);
    font-family: "Open Sans", sans-serif;
  }
  .canvas {
    position: relative; width: 1200px; height: 758px;
  }
  .card {
    position: absolute; top: 224px;
    width: 540px; height: 310px;
    border-radius: 26px;
    overflow: hidden;
    box-shadow: 0 10px 28px rgba(0,0,0,0.18);
  }
  /* Front side */
  .card-front { left: 40px; display: flex; background: var(--card-white); }
  .front-brand {
    width: 282px; height: 100%;
    display: flex; align-items: center; justify-content: center; gap: 14px;
    border-right: 2px solid var(--divider);
  }
  .brand-dot {
    width: 54px; height: 54px; border-radius: 50%;
    background: var(--blue-mid);
  }
  .brand-name {
    font-size: 40px; font-weight: 600; color: var(--ink-dark);
    letter-spacing: 0.5px;
  }
  .front-contact {
    flex: 1; height: 100%;
    background: linear-gradient(180deg, var(--blue-deep) 0%, var(--blue-mid) 50%, var(--blue-light) 100%);
    color: var(--text-on-blue);
    padding: 42px 0 0 36px;
  }
  .person-name { font-size: 19px; font-weight: 700; line-height: 1.2; }
  .person-title { font-size: 13px; margin-bottom: 16px; }
  .contact-list { list-style: none; font-size: 14px; line-height: 1.5; }
  .contact-list li { display: flex; align-items: center; gap: 7px; }
  .contact-list svg { width: 11px; height: 11px; flex: none; fill: var(--text-on-blue); }
  .address { margin-top: 18px; font-size: 14px; line-height: 1.4; }

  /* Back side */
  .card-back {
    left: 620px;
    background: linear-gradient(180deg, var(--blue-deep) 0%, var(--blue-mid) 45%, var(--blue-light) 100%);
  }
  .back-brand {
    position: absolute; left: 34px; top: 0; height: 100%;
    display: flex; flex-direction: column; align-items: center; justify-content: center; gap: 14px;
    width: 190px;
  }
  .back-brand .brand-dot {
    width: 130px; height: 130px;
    background: var(--text-on-blue); opacity: 0.92;
  }
  .back-brand .brand-name { color: var(--text-on-blue); font-size: 30px; }
  .street-photo {
    position: absolute; left: 262px; top: 54px;
    width: 252px; height: 200px;
    border-radius: 14px;
    background: linear-gradient(135deg, var(--photo-light) 0%, var(--photo-grey) 45%, var(--photo-dark) 100%);
    box-shadow: 0 0 18px 6px rgba(255,255,255,0.25);
  }
</style>
</head>
<body>
<main class="canvas">
  <section class="card card-front" aria-label="Business card front">
    <div class="front-brand">
      <span class="brand-dot"></span>
      <span class="brand-name">Nimbora</span>
    </div>
    <div class="front-contact">
      <p class="person-name">Your Name</p>
      <p class="person-title">Title</p>
      <ul class="contact-list">
        <li><svg viewBox="0 0 12 12"><path d="M2.5 1 L4.5 1 L5.2 3.6 L4 4.6 C4.6 6 6 7.4 7.4 8 L8.4 6.8 L11 7.5 L11 9.5 C11 10.3 10.3 11 9.5 11 C5 11 1 7 1 2.5 C1 1.7 1.7 1 2.5 1 Z"/></svg>123-456-789</li>
        <li><svg viewBox="0 0 12 12"><rect x="3" y="0.5" width="6" height="11" rx="1.2"/><rect x="4.2" y="2" width="3.6" height="5.5" fill="#2f6fc4"/></svg>123-456-789</li>
        <li><svg viewBox="0 0 12 12"><rect x="0.5" y="2.5" width="11" height="7.5" rx="1"/><path d="M1 3 L6 7 L11 3" stroke="#2f6fc4" stroke-width="1" fill="none"/></svg>info@nimbora.com</li>
        <li><svg viewBox="0 0 12 12"><circle cx="6" cy="6" r="5.3"/></svg>www.nimbora.com</li>
      </ul>
      <p class="address">Complex name, Street name<br>City, State, zip code</p>
    </div>
  </section>

  <section class="card card-back" aria-label="Business card back">
    <div class="back-brand">
      <span class="brand-dot"></span>
      <span class="brand-name">Nimbora</span>
    </div>
    <div class="street-photo" role="img" aria-label="Photo of cars parked in marked street parking bays beside a city pavement"></div>
  </section>
</main>
</body>
</html>
```